Brightway Haul & Upkeep Services, are a company that offers a 'one stop shop' pre-move clean up a

I have already selected a logo which I would like on the front of the business cards along with phone numbers, web address and email which are:
0487650392
www.brightwayhaul.com.au
brightwayhaulandupkeep@mailbox.example

On the back of the card I would like to list some of the types of service we offer (clean - move - repairs/maintenance) which are:
CLEAN - windows, gutters, solar panels, driveways/paths, carpets.
MOVE - Small/medium size house/office moves, large item pick-up & delivery, yard clean-up and removal.
General maintenance and repairs.

I would like the blue logo on a gray background.

Thanks

```html
<!DOCTYPE html>
<html lang="en">
<head>
<meta charset="utf-8">
<title>Brightway Haul &amp; Upkeep Services – Business Card</title>
<link rel="stylesheet" href="https://fonts.googleapis.com/css2?family=Saira+Semi+Condensed:wght@700&family=Open+Sans:wght@400;600&display=swap">
<style>
  :root {
    --brand-blue: #2a6db5;
    --ink: #2b2b2b;
    --card-light: #f4f4f4;
    --card-mid: #c9cacc;
    --backdrop: #e6e4e1;
    --white: #ffffff;
    --stripe-dark: #000000;
  }
  * { margin: 0; padding: 0; box-sizing: border-box; }
  html, body {
    width: 1200px; height: 790px; overflow: hidden;
    background: var(--backdrop);
  }
  .canvas { position: relative; width: 1200px; height: 790px; }
  .card {
    position: absolute;
    width: 560px; height: 320px;
    background: linear-gradient(170deg, var(--card-light) 0%, #e2e3e4 45%, var(--card-mid) 100%);
    box-shadow: 0 6px 18px rgba(0,0,0,0.18);
    overflow: hidden;
  }
  .card--front { left: 50px; top: 80px; }
  .card--back { left: 590px; top: 390px; }

  .brand { display: flex; align-items: center; gap: 14px; }
  .brand__mark { width: 26px; height: 26px; background: var(--brand-blue); flex: none; }
  .brand__name {
    font-family: "Saira Semi Condensed", "Arial Narrow", sans-serif;
    font-weight: 700; color: var(--brand-blue);
    font-size: 34px; line-height: 1.0; text-transform: uppercase;
  }
  .card--front .brand { position: absolute; left: 56px; top: 46px; }
  .card--back .brand { position: absolute; left: 70px; top: 40px; }

  .contact {
    position: absolute; left: 56px; top: 146px;
    display: flex; gap: 20px;
    font-family: "Open Sans", Arial, sans-serif; font-size: 12.5px; color: var(--ink);
    white-space: nowrap;
  }
  .contact__item { display: flex; align-items: center; gap: 6px; }
  .contact__icon { width: 12px; height: 12px; fill: var(--brand-blue); }

  .swoosh { position: absolute; left: 0; top: 0; width: 560px; height: 320px; }
  .web {
    position: absolute; right: 26px; top: 262px;
    font-family: "Open Sans", Arial, sans-serif; font-weight: 600;
    font-size: 14px; letter-spacing: 2px; color: var(--white);
  }

  .services { position: absolute; left: 0; right: 0; top: 150px; text-align: center; }
  .services__title {
    font-family: "Open Sans", Arial, sans-serif; font-weight: 600;
    color: var(--brand-blue); font-size: 21px; letter-spacing: 7px;
  }
  .services__list {
    list-style: none; margin-top: 10px;
    font-family: "Open Sans", Arial, sans-serif; font-weight: 600;
    color: var(--ink); font-size: 17px; line-height: 1.55;
  }
</style>
</head>
<body>
<main class="canvas">
  <section class="card card--front" aria-label="Business card front">
    <svg class="swoosh" viewBox="0 0 560 320" aria-hidden="true">
      <path d="M0 262 C180 262 350 240 560 184 L560 320 L0 320 Z" fill="var(--stripe-dark)"/>
      <path d="M0 272 C190 270 360 250 560 198 L560 320 L0 320 Z" fill="var(--white)"/>
      <path d="M0 278 C200 276 370 256 560 206 L560 320 L0 320 Z" fill="var(--brand-blue)"/>
    </svg>
    <div class="brand">
      <span class="brand__mark" aria-hidden="true"></span>
      <span class="brand__name">Brightway Haul &amp;<br>Upkeep Services</span>
    </div>
    <div class="contact">
      <span class="contact__item">
        <svg class="contact__icon" viewBox="0 0 24 24" aria-hidden="true"><path d="M6.6 10.8a15.1 15.1 0 0 0 6.6 6.6l2.2-2.2a1 1 0 0 1 1-.25 11.4 11.4 0 0 0 3.6.57 1 1 0 0 1 1 1V20a1 1 0 0 1-1 1A17 17 0 0 1 3 4a1 1 0 0 1 1-1h3.5a1 1 0 0 1 1 1c0 1.25.2 2.45.57 3.57a1 1 0 0 1-.25 1z"/></svg>
        0487650392
      </span>
      <span class="contact__item">
        <svg class="contact__icon" viewBox="0 0 24 24" aria-hidden="true"><path d="M2 5h20v14H2z M3 6l9 7 9-7" fill="var(--brand-blue)" stroke="#fff" stroke-width="1.5"/></svg>
        brightwayhaulandupkeep@mailbox.example
      </span>
    </div>
    <div class="web">www.brightwayhaul.com.au</div>
  </section>

  <section class="card card--back" aria-label="Business card back">
    <div class="brand">
      <span class="brand__mark" aria-hidden="true"></span>
      <span class="brand__name">Brightway Haul &amp;<br>Upkeep Services</span>
    </div>
    <div class="services">
      <h2 class="services__title">Services we offer</h2>
      <ul class="services__list">
        <li>• CLEAN &nbsp;• MOVE</li>
        <li>• GENERAL MAINTENANCE AND REPAIRS.</li>
      </ul>
    </div>
  </section>
</main>
</body>
</html>
```